KR Appraisals website redesign

I would like to refresh my existing website of www.krappraisals-example.com with new graphics, look and feel, as well as updated structure and wording. Content and layout changes have been uploaded to this project Brief.

My existing website has a dark feel. I am now looking for a light and energetic feel. Financial Services is my industry, so the website should be reflect that. I would also like to reflect the concepts of Trust, Service and Expertise.

The website must be serious and upmarket.

Target Market(s)

Corporate board members, CFO's, treasurers and controllers
Auditors, tax advisors, private equity and venture capital asset managers, investors, tax authorities

Industry/Entity Type

Financial Service

Coding

Coded - Design and coding required

Number of Pages Required

5+ page

Font styles to use
Sans Serif
Other font styles liked:
• Designer can choose another modern font

Colors
0355a3
3277b5
85acd3
eaf1f7
f37122
f68d4d
9bcb3c
acd037
cadf82

Requirements
Must have
• Good hi resolution pictures that convey "Finance", "Trust", "Service" or "Expertise".
• An anti-bot (such as Captcha) mechanism in the contact form.
Should not have
• Must not have all content on one rolling screen.

```html
<!DOCTYPE html>
<html lang="en">
<head>
<meta charset="utf-8">
<title>KR Appraisals</title>
<link href="https://fonts.googleapis.com/css2?family=Lato:wght@400;700&family=Tenor+Sans&display=swap" rel="stylesheet">
<style>
:root{
  --orange:#f37122;
  --orange-soft:#f68d4d;
  --blue:#0355a3;
  --blue-mid:#3277b5;
  --blue-light:#85acd3;
  --blue-pale:#eaf1f7;
  --ink:#333333;
  --muted:#555555;
  --dark:#454545;
  --paper:#ffffff;
  --bg:#f7f7f7;
}
*{box-sizing:border-box;margin:0;padding:0}
html,body{width:1200px;height:2789px;overflow:hidden}
body{position:relative;background:var(--paper);font-family:'Lato',sans-serif;color:var(--ink)}
.abs{position:absolute}
.caps{font-family:'Tenor Sans',sans-serif;font-variant:small-caps;letter-spacing:.5px}
.btn{position:absolute;background:var(--orange);color:#fff;border-radius:22px;font-size:14px;display:flex;align-items:center;justify-content:center}

/* header */
.site-header{left:0;top:0;width:1200px;height:128px;background:var(--bg)}
.brand{display:flex;align-items:center;gap:12px;font-size:28px;color:#555;letter-spacing:1px}
.brand-square{width:20px;height:20px;background:currentColor}
.nav a{position:absolute;top:64px;font-size:14px;color:var(--ink);text-decoration:none}
.nav a.active{color:var(--orange)}
.nav a.active::after{content:"";position:absolute;left:0;right:0;top:22px;height:2px;background:var(--orange)}
.call-icon{left:976px;top:57px;width:28px;height:28px;border-radius:50%;background:var(--orange)}
.call-label{left:1012px;top:55px;font-size:12px;color:var(--orange)}
.call-number{left:1012px;top:70px;font-size:13px;color:var(--ink)}

/* hero */
.hero{left:0;top:128px;width:1200px;height:560px;background:linear-gradient(100deg,#5b4a43 0%,#9a8a80 30%,#d9d6d2 55%,#c9ccd2 75%,#7f8893 100%)}
.hero-title{left:137px;top:336px;font-size:34px;line-height:38px;color:#fff}
.hero-wave{left:0;top:620px}
.arrow{top:384px}
.dots span{position:absolute;top:646px;width:7px;height:7px;border-radius:50%;background:#fff}

/* about */
.section-title{position:absolute;left:0;width:1200px;text-align:center;font-size:34px;color:#333}
.about-text{left:225px;top:805px;width:750px;text-align:center;font-size:14px;line-height:17px;color:var(--ink)}
.about-text p{margin-bottom:16px}

/* services */
.card{position:absolute;width:327px;height:309px;background:#fff;box-shadow:0 0 8px rgba(0,0,0,.08);text-align:center}
.card-intro{background:var(--orange);text-align:left;color:#fff;box-shadow:none}
.card-intro .intro-mark{position:absolute;left:37px;top:42px;width:42px;height:42px;border:3px solid #fff}
.card-intro h2{position:absolute;left:36px;top:92px;font-size:40px;line-height:44px;font-weight:400}
.card-intro p{position:absolute;left:36px;top:184px;width:265px;font-size:13px;line-height:16px}
.card-icon{position:absolute;left:113px;width:100px;height:90px}
.card h3{position:absolute;left:10px;width:307px;font-size:23px;line-height:28px;font-weight:400;color:#333}
.card p.desc{position:absolute;left:30px;width:267px;font-size:13px;line-height:16px;color:var(--muted)}
.card .corner{position:absolute;right:6px;bottom:6px}

/* news */
.news{position:absolute;top:1871px;width:342px;height:360px;background:#fff;box-shadow:0 0 8px rgba(0,0,0,.08)}
.news-img{position:absolute;left:12px;top:10px;width:318px;height:199px}
.news-date{position:absolute;left:27px;top:180px;width:41px;height:42px;background:#3a3a3a;color:#fff;font-size:14px;line-height:15px;text-align:center;padding-top:6px}
.news h4{position:absolute;left:27px;top:240px;font-size:14px;font-weight:400;color:#333}
.news p{position:absolute;left:27px;top:264px;width:295px;font-size:13px;line-height:16px;color:var(--muted)}
.news a{position:absolute;left:28px;top:326px;font-size:14px;color:var(--blue)}

/* footer */
.city{left:0;top:2250px;width:1200px;height:220px;background:linear-gradient(180deg,rgba(234,241,247,0) 0%,var(--blue-pale) 100%)}
.footer{left:0;top:2380px;width:1200px;height:350px}
.foot-brand{left:80px;top:2515px;width:243px;height:102px;display:flex;align-items:center;justify-content:center;color:#fff}
.foot-h{font-size:16px;color:#fff;top:2493px}
.foot-h::after{content:"";position:absolute;left:0;top:28px;width:45px;height:2px;background:var(--orange)}
.foot-list{list-style:disc;color:#fff;font-size:14px;line-height:24px}
.foot-contact{font-size:14px;line-height:24px;color:#fff}
.field{position:absolute;border:1px solid #ddd;color:#fff;font-size:13px;padding:7px 10px}
.captcha{position:absolute;left:857px;top:2646px;width:260px;height:30px;display:flex;align-items:center;gap:8px;font-size:12px;color:#fff;border:1px solid #777;padding:0 8px}
.captcha-box{width:16px;height:16px;border:1px solid var(--blue-light);background:#fff}
.captcha-mark{margin-left:auto;width:14px;height:14px;border-radius:50%;background:var(--blue-mid)}
.bottom-bar{left:0;top:2730px;width:1200px;height:59px;background:#f5f5f5}
.social{top:2746px;width:30px;height:30px;border-radius:50%;border:2px solid #555}
</style>
</head>
<body>

<header class="abs site-header">
  <div class="abs brand" style="left:80px;top:44px"><span class="brand-square"></span>KR Appraisals</div>
  <nav class="nav">
    <a class="active" href="#" style="left:525px">Home</a>
    <a href="#" style="left:609px">About</a>
    <a href="#" style="left:695px">Services ˅</a>
    <a href="#" style="left:793px">News</a>
    <a href="#" style="left:875px">Contact</a>
  </nav>
  <div class="abs call-icon"><svg width="28" height="28" viewBox="0 0 28 28"><path d="M10 8l3 3-2 2c1 2 3 4 5 5l2-2 3 3-2 2c-5 0-11-6-11-11z" fill="#fff"/></svg></div>
  <div class="abs call-label">Call Us Now</div>
  <div class="abs call-number">+31 20 555 0147</div>
</header>

<section>
  <div class="abs hero" role="img" aria-label="Business presentation in a bright meeting room with a finance and growth illustration"></div>
  <svg class="abs arrow" style="left:22px" width="36" height="20" viewBox="0 0 36 20"><path d="M35 10H2M10 2L2 10l8 8" stroke="#fff" stroke-width="2" fill="none"/></svg>
  <svg class="abs arrow" style="left:1138px" width="36" height="20" viewBox="0 0 36 20"><path d="M1 10h33M26 2l8 8-8 8" stroke="#fff" stroke-width="2" fill="none"/></svg>
  <h1 class="abs hero-title caps" style="font-weight:400">Business &amp; Intellectual<br>Property Valuations</h1>
  <div class="btn" style="left:136px;top:426px;width:162px;height:42px">Read More</div>
  <div class="dots"><span style="left:1062px;background:var(--orange)"></span><span style="left:1078px"></span><span style="left:1094px"></span><span style="left:1110px"></span></div>
  <svg class="abs hero-wave" width="1200" height="70" viewBox="0 0 1200 70"><path d="M0 22C150 -8 350 0 600 30S1000 75 1200 40V70H0z" fill="#fff"/><path d="M0 22C150 -8 350 0 600 30S1000 75 1200 40" stroke="#555" stroke-width="1.5" fill="none"/></svg>
</section>

<section>
  <h2 class="section-title caps" style="top:722px;font-weight:400">About us</h2>
  <svg class="abs" style="left:530px;top:770px" width="142" height="12" viewBox="0 0 142 12"><path d="M2 8C40 0 100 0 140 6C100 3 40 4 2 10z" fill="#555"/></svg>
  <div class="abs about-text">
    <p>KR Appraisals, founded in 2012, is a boutique corporate finance practice servicing companies throughout Europe and North America. Our office is located in the Netherland in the Westhaven Science Park. Our clients come from a broad range of industries with valuations ranging between micro-cap and large-cap.</p>
    <p>KR Appraisals assists companies with valuations of businesses and intellectual property, M&amp;A advisory, business plan coaching and purchase price allocation (PPA). Through our bespoke approach and global network, we customize teams to the needs of our clients.</p>
    <p>Trust, Service and Expertise are the 3 pillars of KR Appraisals. Trust is paramount.<br>Clients rely on KR Appraisals Services...</p>
  </div>
  <div class="btn" style="left:520px;top:991px;width:163px;height:42px">Read More</div>
</section>

<section>
  <div class="card card-intro" style="left:79px;top:1099px">
    <div class="intro-mark"></div>
    <h2 class="caps">Our<br>Services</h2>
    <p>Lorem Ipsum is simply dummy text of the printing and typesetting industry. Lorem has been the industry's standard dummy text ever since the 1500s,</p>
  </div>

  <div class="card" style="left:436px;top:1099px">
    <svg class="card-icon" style="top:36px" viewBox="0 0 100 90" role="img" aria-label="Hand holding a dollar coin icon" fill="none" stroke="#333" stroke-width="2.5">
      <circle cx="62" cy="30" r="20" fill="var(--orange)" stroke="#333"/>
      <text x="62" y="38" text-anchor="middle" font-family="Lato,sans-serif" font-size="22" fill="#333" stroke="none">$</text>
      <path d="M12 62h18l16 6h18c4 0 4 6 0 6H44M30 80h32l30-20c3-3 0-7-4-5L66 68"/>
      <rect x="4" y="58" width="10" height="26"/>
      <path d="M14 34l8-8 6 5 10-10"/>
    </svg>
    <h3 class="caps" style="top:146px">Business Valuation</h3>
    <p class="desc" style="top:186px">Lorem Ipsum is simply dummy text of the printing and typesetting industry. Lorem has been the industry's standard dummy text ever since the 1500s,</p>
    <svg class="corner" width="60" height="56"><path d="M60 0V56H0z" fill="var(--orange)"/><path d="M43 30v16M35 38h16" stroke="#fff" stroke-width="2"/></svg>
  </div>

  <div class="card" style="left:792px;top:1099px">
    <svg class="card-icon" style="top:36px" viewBox="0 0 100 90" role="img" aria-label="Gears and balance scale icon" fill="none" stroke="#333" stroke-width="2.5">
      <circle cx="30" cy="40" r="18" stroke-dasharray="6 3"/>
      <circle cx="30" cy="40" r="8"/>
      <circle cx="52" cy="62" r="11" fill="var(--orange)"/>
      <circle cx="52" cy="62" r="4" fill="#fff"/>
      <path d="M78 10v60M66 70h24M62 20h32M62 20l-8 20h16zM94 20l-8 20h16"/>
      <path d="M54 40a8 5 0 0016 0M86 40a8 5 0 0016 0" stroke="var(--orange)"/>
    </svg>
    <h3 class="caps" style="top:146px">Intellectual Property<br>Valuation</h3>
    <p class="desc" style="top:206px">Lorem Ipsum is simply dummy text of the printing and typesetting industry. Lorem has been the industry's standard dummy text ever since the 1500s,</p>
    <svg class="corner" width="60" height="56"><path d="M60 0V56H0z" fill="var(--orange)"/><path d="M43 30v16M35 38h16" stroke="#fff" stroke-width="2"/></svg>
  </div>

  <div class="card" style="left:79px;top:1436px">
    <svg class="card-icon" style="top:30px" viewBox="0 0 100 90" role="img" aria-label="Business plan document icon" fill="none" stroke="#333" stroke-width="2.5">
      <rect x="20" y="4" width="58" height="78" rx="2"/>
      <path d="M28 16h42M28 24h30"/>
      <circle cx="34" cy="40" r="4"/><circle cx="62" cy="40" r="4"/><circle cx="34" cy="62" r="4"/>
      <path d="M38 40h20M34 44v14M62 44c0 12-10 18-24 18"/>
      <rect x="58" y="56" width="28" height="26" fill="var(--orange)"/>
      <path d="M66 62v12l6-4 6 4V62"/>
    </svg>
    <h3 class="caps" style="top:126px">Business Plan<br>Coaching</h3>
    <p class="desc" style="top:188px">Lorem Ipsum is simply dummy text of the printing and typesetting industry. Lorem has been the industry's standard dummy text ever since the 1500s,</p>
    <svg class="corner" width="60" height="56"><path d="M60 0V56H0z" fill="var(--orange)"/><path d="M43 30v16M35 38h16" stroke="#fff" stroke-width="2"/></svg>
  </div>

  <div class="card" style="left:436px;top:1436px">
    <svg class="card-icon" style="top:36px" viewBox="0 0 100 90" role="img" aria-label="Two advisors talking icon" fill="none" stroke="#333" stroke-width="2.5">
      <rect x="36" y="4" width="40" height="22" rx="3" fill="var(--orange)"/>
      <path d="M42 26l-4 8 10-8"/>
      <circle cx="48" cy="15" r="2" fill="#fff"/><circle cx="56" cy="15" r="2" fill="#fff"/><circle cx="64" cy="15" r="2" fill="#fff"/>
      <circle cx="28" cy="52" r="9"/><circle cx="72" cy="52" r="9"/>
      <path d="M12 86V76c0-8 8-12 16-12s16 4 16 12v10M56 86V76c0-8 8-12 16-12s16 4 16 12v10"/>
    </svg>
    <h3 class="caps" style="top:138px">M&amp;A Advisory</h3>
    <p class="desc" style="top:188px">Lorem Ipsum is simply dummy text of the printing and typesetting industry. Lorem has been the industry's standard dummy text ever since the 1500s,</p>
    <svg class="corner" width="60" height="56"><path d="M60 0V56H0z" fill="var(--orange)"/><path d="M43 30v16M35 38h16" stroke="#fff" stroke-width="2"/></svg>
  </div>

  <div class="card" style="left:792px;top:1436px">
    <svg class="card-icon" style="top:28px" viewBox="0 0 100 90" role="img" aria-label="Dollar pie chart icon" fill="none" stroke="#333" stroke-width="2.5">
      <path d="M52 8a38 38 0 0130 52L52 46z" fill="var(--orange)"/>
      <circle cx="48" cy="48" r="36"/>
      <circle cx="48" cy="48" r="14"/>
      <text x="48" y="55" text-anchor="middle" font-family="Lato,sans-serif" font-size="18" fill="#333" stroke="none">$</text>
      <path d="M48 12v22M16 48h18M62 48h22M48 62v22" stroke-width="2"/>
      <path d="M76 6h14" />
    </svg>
    <h3 class="caps" style="top:122px">Purchase Price<br>Allocation</h3>
    <p class="desc" style="top:188px">Lorem Ipsum is simply dummy text of the printing and typesetting industry. Lorem has been the industry's standard dummy text ever since the 1500s,</p>
    <svg class="corner" width="60" height="56"><path d="M60 0V56H0z" fill="var(--orange)"/><path d="M43 30v16M35 38h16" stroke="#fff" stroke-width="2"/></svg>
  </div>
</section>

<div class="abs city" role="img" aria-label="Faint city skyline backdrop"></div>

<section>
  <h2 class="section-title caps" style="top:1812px;left:12px;font-weight:400">Latest News</h2>

  <article class="news" style="left:68px">
    <div class="news-img" role="img" aria-label="Businessman celebrating at his laptop" style="background:linear-gradient(135deg,#e9ecef,#bfc4c8 55%,#3d3f44)"></div>
    <div class="news-date caps">02<br>Oct</div>
    <h4 class="caps">What is Lorem Ipsum?</h4>
    <p>Lorem ipsum dolor sit amet, consectetur adipiscing elit, sed do eiusmod tempor incididunt ut labore et dolore magna aliqua.</p>
    <a href="#">Read More</a>
  </article>

  <article class="news" style="left:425px">
    <div class="news-img" role="img" aria-label="Hand tapping a tablet showing charts" style="background:linear-gradient(135deg,#1d3550,#3277b5 55%,#b9d3ea)"></div>
    <div class="news-date caps">02<br>Oct</div>
    <h4 class="caps">What is Lorem Ipsum?</h4>
    <p>Lorem Ipsum is simply dummy the printing and typesetting industry. Lorem Ipsum has been the standard dummy.</p>
    <a href="#">Read More</a>
  </article>

  <article class="news" style="left:788px">
    <div class="news-img" role="img" aria-label="Two colleagues reviewing documents together" style="background:linear-gradient(135deg,#d9dde2,#85acd3 50%,#4c5f78)"></div>
    <div class="news-date caps">02<br>Oct</div>
    <h4 class="caps">What is Lorem Ipsum?</h4>
    <p>Lorem Ipsum is simply dummy the printing and typesetting industry. Lorem Ipsum has been the standard dummy.</p>
    <a href="#">Read More</a>
  </article>

  <div class="btn" style="left:519px;top:2263px;width:163px;height:42px">View More</div>
</section>

<footer>
  <svg class="abs footer" width="1200" height="350" viewBox="0 0 1200 350"><path d="M0 20C200 -15 500 10 800 45S1100 50 1200 40V350H0z" fill="var(--dark)"/></svg>
  <div class="abs brand foot-brand" style="font-size:27px;color:#fff"><span class="brand-square"></span>KR Appraisals</div>

  <div class="abs foot-h caps" style="left:439px">Quick Link</div>
  <ul class="abs foot-list" style="left:459px;top:2535px">
    <li>Home</li><li>About</li><li>Services</li><li>News</li><li>Contact</li>
  </ul>

  <div class="abs foot-h caps" style="left:620px">Quick Contact</div>
  <svg class="abs" style="left:619px;top:2541px" width="14" height="16" viewBox="0 0 14 16"><path d="M7 15C3 10 2 8 2 6a5 5 0 0110 0c0 2-1 4-5 9z" stroke="#ccc" fill="none"/><circle cx="7" cy="6" r="2" stroke="#ccc" fill="none"/></svg>
  <svg class="abs" style="left:618px;top:2613px" width="16" height="14" viewBox="0 0 16 14"><rect x="2" y="5" width="12" height="8" stroke="#ccc" fill="none"/><path d="M1 5c4-4 10-4 14 0" stroke="#ccc" fill="none"/></svg>
  <svg class="abs" style="left:618px;top:2639px" width="16" height="12" viewBox="0 0 16 12"><rect x="1" y="1" width="14" height="10" stroke="#ccc" fill="none"/><path d="M1 1l7 6 7-6" stroke="#ccc" fill="none"/></svg>
  <div class="abs foot-contact" style="left:650px;top:2535px">Veldweg 42<br>1234 AB Westhaven<br>The Netherlands<br>+31 20 555 0147<br>info@kr-example.com</div>

  <div class="abs foot-h caps" style="left:857px">Contact Us</div>
  <div class="field" style="left:857px;top:2542px;width:126px;height:32px">Name</div>
  <div class="field" style="left:990px;top:2542px;width:127px;height:32px">Phone</div>
  <div class="field" style="left:857px;top:2583px;width:260px;height:55px">Message</div>
  <div class="captcha"><span class="captcha-box"></span>I'm not a robot<span class="captcha-mark"></span></div>
  <div class="btn" style="left:857px;top:2684px;width:167px;height:36px;font-size:13px">Send</div>

  <div class="abs bottom-bar"></div>
  <div class="abs" style="left:79px;top:2752px;font-size:14px;color:#333">Copyright © 2019 KR Appraisals. All Right Reserve</div>
  <div class="abs social" style="left:945px;background:var(--orange);border-color:var(--orange)"></div>
  <div class="abs social" style="left:992px"></div>
  <div class="abs social" style="left:1039px"></div>
  <div class="abs social" style="left:1086px"></div>
</footer>

</body>
</html>
```